Healthy Food Healthy Brain Rack Card

We want a new 2 page (front and page) 3.67" x 8.5" rack card. This rack card is the first of a series we are creating. We will have five more eventually.

The minimum font size for the text on the front is 11 point and also for other main body text.

Use the text on the word document.

The images and layout in the word document are just sample ideas we had.

We have a subscripton to plivora pics images so prefer to get images from there or free high quality images.

The document is for older readers. Do not put text over graphics and keep it simple and easy to read with high contrast.

We are open to any color scheme, though something that conveys fresh and healthy, is good.

We want some very simple design element(s) incorporated that convey Native American communities or heritage. But NO head dress, teepee graphics, etc.

At the top, of the first page we would like a collage of healthy food images. This can include fish, chicken, fresh vegetables, berries, brown rice, etc.

On the back side, the text below the brown box on the word document with the title "mock up" can be smaller as needed.

Please remember to include the funding statement - it can be in a very small font 6/7 point.

For more information about our project, please visit https://veltronaq.org/mind-care/

```html
<!DOCTYPE html>
<html lang="en">
<head>
<meta charset="utf-8">
<title>Healthy Heart, Healthy Brain – Rack Card</title>
<link rel="stylesheet" href="https://fonts.googleapis.com/css2?family=Antonio:wght@600;700&family=Oswald:wght@500;600&family=Montserrat:wght@600;700&family=Archivo+Narrow:wght@400;500;600&display=swap">
<style>
  :root {
    --teal: #23777a;
    --teal-dark: #1b5f62;
    --brown: #6c2f2c;
    --brown-dark: #552321;
    --ink: #231f20;
    --paper: #ffffff;
    --backdrop: #e9eaec;
    --rule: #9a9a9a;
  }
  * { box-sizing: border-box; margin: 0; padding: 0; }
  html, body { width: 1200px; height: 2193px; overflow: hidden; background: var(--backdrop); }
  body { position: relative; font-family: "Archivo Narrow", "Arial Narrow", sans-serif; color: var(--ink); }

  .card-slot { position: absolute; top: 448px; width: 560px; height: 1296px; }
  .card-slot--front { left: 20px; }
  .card-slot--back { left: 620px; }
  .card {
    position: absolute; left: 0; top: 0; width: 525px; height: 1215px;
    background: var(--paper); transform: scale(1.0667); transform-origin: 0 0;
    box-shadow: 0 2px 10px rgba(0,0,0,.12); overflow: hidden;
  }

  /* brand lockup */
  .brand { position: absolute; left: 0; right: 0; display: flex; align-items: center; justify-content: center; gap: 12px; }
  .brand__dot { width: 58px; height: 58px; border-radius: 50%; background: var(--teal); flex: none; }
  .brand__name { font-family: "Montserrat", sans-serif; font-weight: 600; color: var(--teal); font-size: 17px; line-height: 1.1; }
  .brand__name small { display: block; font-size: 9.5px; letter-spacing: .3px; }

  /* front */
  .photo { position: absolute; }
  .photo--seafood { left: 0; top: 110px; width: 278px; height: 132px;
    background: linear-gradient(135deg, #2d2c2e 0%, #6d6a6a 45%, #c8552e 70%, #3a3a3c 100%); }
  .photo--fruit { left: 0; top: 254px; width: 278px; height: 133px;
    background: linear-gradient(160deg, #9db24c 0%, #e7a03a 40%, #b5273a 70%, #5c4656 100%); }
  .photo--veg { left: 294px; top: 110px; width: 231px; height: 277px;
    background: linear-gradient(165deg, #4b5a2c 0%, #2f3a24 25%, #c62828 55%, #f2a81d 80%, #3b3b33 100%); }

  .headline { position: absolute; top: 404px; left: 0; right: 0; text-align: center; white-space: nowrap;
    font-family: "Antonio", "Oswald", sans-serif; font-weight: 700; font-size: 44px; line-height: 52px; letter-spacing: -.5px; color: var(--ink); }
  .headline em { font-style: normal; color: var(--brown); }
  .divider { position: absolute; top: 462px; left: 55px; width: 415px; height: 1px; background: var(--rule); }
  .divider::after { content: ""; position: absolute; left: 50%; top: -2px; width: 40px; height: 5px; margin-left: -20px; border-radius: 3px; background: var(--brown); }

  .intro { position: absolute; top: 477px; left: 45px; right: 45px; text-align: center; font-size: 17px; line-height: 24px; }

  .panel { position: absolute; left: 35px; width: 455px; border-radius: 22px; }
  .tab { position: absolute; text-align: center; color: #fff; font-family: "Montserrat", sans-serif; font-weight: 700; border-radius: 22px 22px 26px 26px; }

  .steps { top: 597px; height: 390px; background: var(--teal); }
  .steps .tab { top: -16px; left: 65px; width: 325px; height: 54px; background: var(--brown); font-size: 17px; line-height: 19px; padding-top: 8px; }
  .steps__cols { position: absolute; top: 62px; left: 30px; right: 20px; display: flex; gap: 14px; }
  .steps__col { flex: 1; list-style: none; }
  .steps__col li { display: flex; gap: 8px; color: #fff; font-size: 16.5px; line-height: 20px; margin-bottom: 18px; }
  .steps__col--right li { margin-bottom: 19px; }
  .tick { width: 15px; height: 15px; flex: none; margin-top: 3px; }
  .steps__note { position: absolute; bottom: 16px; left: 0; right: 0; text-align: center; color: #fff; font-size: 16.5px; line-height: 24px; }

  .cta { position: absolute; top: 1005px; left: 0; right: 0; text-align: center; font-family: "Montserrat", sans-serif; font-weight: 700; color: var(--brown); font-size: 17px; line-height: 22px; }
  .quote { position: absolute; top: 1054px; left: 45px; right: 40px; padding-left: 26px; text-align: center; font-size: 16.5px; line-height: 23px; }
  .quote__mark { position: absolute; left: 0; top: -4px; font-family: "Montserrat", sans-serif; font-weight: 700; font-size: 30px; line-height: 30px; color: var(--brown); }
  .quote cite { display: block; font-style: normal; font-family: "Montserrat", sans-serif; font-weight: 700; color: var(--teal); font-size: 13.5px; letter-spacing: .3px; }

  .footer-rule { position: absolute; left: 0; right: 0; height: 4px; background: var(--teal); }
  .footer { position: absolute; left: 0; right: 0; bottom: 0; background: var(--brown); color: #fff; text-align: center; }
  .card--front .footer-rule { top: 1135px; }
  .card--front .footer { height: 73px; font-family: "Montserrat", sans-serif; font-weight: 700; font-size: 18px; letter-spacing: 1.5px; line-height: 73px; }

  /* back */
  .banner { position: absolute; top: 32px; left: 32px; width: 457px; height: 62px; background: var(--teal); border-radius: 22px 22px 0 0;
    color: #fff; text-align: center; font-family: "Montserrat", sans-serif; font-weight: 700; font-size: 26px; letter-spacing: 1.5px; padding-top: 9px; }
  .banner__sub { position: absolute; top: 80px; left: 55px; width: 412px; height: 34px; border-radius: 17px; background: var(--brown);
    color: #fff; text-align: center; font-family: "Montserrat", sans-serif; font-weight: 700; font-size: 15px; letter-spacing: .8px; line-height: 34px; }

  .ingredients { top: 150px; left: 32px; width: 457px; height: 350px; background: var(--brown); }
  .ingredients .tab { top: -16px; left: 90px; width: 277px; height: 44px; background: var(--teal); font-size: 22px; letter-spacing: 1.5px; line-height: 44px; }
  .ingredients__cols { position: absolute; top: 40px; left: 40px; right: 20px; display: flex; }
  .ingredients__col { list-style: none; flex: 1; }
  .ingredients__col li { display: flex; gap: 10px; color: #fff; font-family: "Oswald", sans-serif; font-weight: 500; font-size: 16px; line-height: 17px; margin-bottom: 13px; }
  .ingredients__col--left { flex: 1.15; }
  .ingredients__art { position: absolute; left: 50px; right: 60px; bottom: 30px; height: 108px; border-radius: 50px;
    background: radial-gradient(ellipse at 20% 60%, #f4c430 0 18%, transparent 30%),
                radial-gradient(ellipse at 55% 65%, #ef7a4f 0 22%, transparent 36%),
                radial-gradient(ellipse at 80% 55%, #6b2f4f 0 18%, transparent 30%),
                radial-gradient(ellipse at 45% 30%, #3f8a2e 0 20%, transparent 40%),
                rgba(255,255,255,.06); }

  .method { position: absolute; top: 512px; left: 35px; right: 35px; text-align: center; font-size: 16.5px; line-height: 24px; }

  .heritage { position: absolute; top: 668px; left: 32px; width: 457px; height: 118px; border: 2px solid var(--teal); border-radius: 20px;
    color: var(--teal); text-align: center; font-family: "Montserrat", sans-serif; font-weight: 700; font-size: 13.5px; line-height: 17px; padding: 16px 40px 0; }

  .info { top: 815px; left: 32px; width: 457px; height: 210px; border: 2px solid var(--teal); }
  .info .tab { top: -18px; left: 65px; width: 323px; height: 40px; background: var(--teal); font-size: 17px; letter-spacing: 1.2px; line-height: 40px; }
  .info__block { position: absolute; font-size: 14px; line-height: 20px; }
  .info__title { display: block; font-family: "Oswald", sans-serif; font-weight: 500; font-size: 16px; color: var(--brown); }
  .info__org { color: var(--brown); }
  .info__block--eating { top: 30px; left: 0; right: 0; text-align: center; }
  .info__block--brain-title { top: 92px; left: 0; right: 0; text-align: center; }
  .info__block--center { top: 118px; left: 18px; width: 210px; }
  .info__block--program { top: 118px; left: 246px; width: 200px; }

  .card--back .brand { top: 1038px; }
  .card--back .brand__dot { width: 50px; height: 50px; }
  .card--back .footer-rule { top: 1102px; }
  .card--back .footer { height: 105px; font-size: 8.6px; line-height: 12px; padding: 14px 40px 0; }
</style>
</head>
<body>

<svg width="0" height="0" style="position:absolute" aria-hidden="true">
  <symbol id="tick" viewBox="0 0 16 16">
    <circle cx="8" cy="8" r="8" fill="#fff"/>
    <path d="M4.3 8.3l2.5 2.4 4.9-5.2" fill="none" stroke="#555" stroke-width="2" stroke-linecap="round" stroke-linejoin="round"/>
  </symbol>
</svg>

<!-- Front -->
<div class="card-slot card-slot--front">
  <article class="card card--front">
    <div class="brand" style="top:35px">
      <span class="brand__dot"></span>
      <span class="brand__name">CEDAR CIRCLE<small>RESOURCE CENTER FOR BRAIN HEALTH</small></span>
    </div>

    <div class="photo photo--seafood" role="img" aria-label="Fresh fish, shellfish and seafood on a dark board"></div>
    <div class="photo photo--fruit" role="img" aria-label="Fresh fruit including apricots, apples, grapes and plums"></div>
    <div class="photo photo--veg" role="img" aria-label="Fresh vegetables: peppers, cucumbers, onions, carrots and garlic"></div>

    <h1 class="headline">HEALTHY HEART, <em>HEALTHY BRAIN</em></h1>
    <div class="divider"></div>

    <p class="intro">Everyone slows down as they get older, both in body and mind. Eating healthier food can help your overall health, including brain health. It may also reduce your risk for memory loss and problems thinking.</p>

    <section class="panel steps">
      <h2 class="tab">Healthier steps to protect<br>your brain</h2>
      <div class="steps__cols">
        <ul class="steps__col">
          <li><svg class="tick"><use href="#tick"/></svg>Eat more vegetables, fruits, whole grains, and lower-fat milk</li>
          <li><svg class="tick"><use href="#tick"/></svg>Use less salt and added sugar</li>
          <li><svg class="tick"><use href="#tick"/></svg>Eat more fish, chicken, turkey, beans, and nuts</li>
          <li><svg class="tick"><use href="#tick"/></svg>Cut down on bad fats (“saturated” and trans), cholesterol, and red meat</li>
        </ul>
        <ul class="steps__col steps__col--right">
          <li><svg class="tick"><use href="#tick"/></svg>Buy fresh, not packaged food when you can</li>
          <li><svg class="tick"><use href="#tick"/></svg>Limit how much alcohol you drink</li>
          <li><svg class="tick"><use href="#tick"/></svg>Learn your daily calorie needs for your body size</li>
          <li><svg class="tick"><use href="#tick"/></svg>Take care of your mental and spiritual health to support your physical and brain health</li>
        </ul>
      </div>
      <p class="steps__note">Small changes can make a big difference for<br>better brain health.</p>
    </section>

    <p class="cta">Talk to your doctor about more steps<br>to healthier food choices.</p>
    <blockquote class="quote">
      <span class="quote__mark">“</span>
      Without the elk, salmon, huckleberries, shellfish, and cedar trees we are nobody…
      <cite>Marla Tenwick (Riverbend)</cite>
    </blockquote>

    <div class="footer-rule"></div>
    <footer class="footer">www.veltronaq.org</footer>
  </article>
</div>

<!-- Back -->
<div class="card-slot card-slot--back">
  <article class="card card--back">
    <h2 class="banner">MAKE THIS AT HOME</h2>
    <p class="banner__sub">Grilled Salmon and Veggie Foil Packets</p>

    <section class="panel ingredients">
      <h3 class="tab">INGREDIENTS</h3>
      <div class="ingredients__cols">
        <ul class="ingredients__col ingredients__col--left">
          <li><svg class="tick"><use href="#tick"/></svg>Salmon</li>
          <li><svg class="tick"><use href="#tick"/></svg>Asparagus</li>
          <li><svg class="tick"><use href="#tick"/></svg>Red or Green Peppers<br>(Or any seasonal<br>vegetable)</li>
          <li><svg class="tick"><use href="#tick"/></svg>Onion</li>
        </ul>
        <ul class="ingredients__col">
          <li><svg class="tick"><use href="#tick"/></svg>Lemon – sliced</li>
          <li><svg class="tick"><use href="#tick"/></svg>Basil</li>
          <li><svg class="tick"><use href="#tick"/></svg>Olive Oil</li>
          <li><svg class="tick"><use href="#tick"/></svg>Salt and Pepper</li>
          <li><svg class="tick"><use href="#tick"/></svg>Garlic Powder</li>
        </ul>
      </div>
      <div class="ingredients__art" role="img" aria-label="Salmon fillet, lemon halves, chili peppers, red onions and a spoon of garlic powder"></div>
    </section>

    <p class="method">Cut asparagus, peppers, and onion into bite-size pieces. Cut salmon into 4-6 oz pieces. Tear tin foil large enough to wrap around salmon &amp; veggies (2 layers). Add veggies and salmon to foil. Drizzle with olive oil, season with salt, pepper, basil, garlic &amp; top with a piece of sliced lemon. Wrap foil tightly around food. Grill at 400 degrees for about 20 minutes. Careful opening</p>

    <p class="heritage">Food &amp; drink are a source of strength and connection to community. A return to traditional food pathways and eating local, seasonal fresh foods make healthier eating easier</p>

    <section class="panel info">
      <h3 class="tab">FOR MORE INFORMATION</h3>
      <div class="info__block info__block--eating">
        <span class="info__title">About Healthier Eating</span>
        <span class="info__org">PlateWise Guide</span><br>
        https://www.platewiseguide.org
      </div>
      <div class="info__block info__block--brain-title"><span class="info__title">About Brain Health</span></div>
      <div class="info__block info__block--center">
        <span class="info__org">Cedar Circle Resource Center</span><br>
        for Brain Health<br>
        https://www.cedarcirclebrain.org
      </div>
      <div class="info__block info__block--program">
        <span class="info__org">Regional Memory Health Program</span><br>
        https://www.rmhp.org/aging
      </div>
    </section>

    <div class="brand">
      <span class="brand__dot"></span>
      <span class="brand__name">CEDAR CIRCLE<small>RESOURCE CENTER FOR BRAIN HEALTH</small></span>
    </div>

    <div class="footer-rule"></div>
    <footer class="footer">This product is supported by the National Wellness Agency (NWA) of the Office of Public Health Services (OPHS) as part of a financial assistance award totaling $348,711 with 100 percent funded by NWA/OPHS. The contents are those of the author(s) and do not necessarily represent the official views of, nor an endorsement, by NWA/OPHS, or the Government.</footer>
  </article>
</div>

</body>
</html>
```